I need 2 flyers designed for my business

Both can be similar in design and will have different purposes. I need an education based flyer and I need a government based flyer. The focus of the flyer will be software on the front and services on the back.
These all need to be 8.5x 11 in dimension (they can be full bleed). I would like to be able to print these out if needed. The design needs to look good with our website > www.brelmont.com

The software details are on the website.

```html
<!DOCTYPE html>
<html lang="en">
<head>
<meta charset="utf-8">
<title>Brelmont Flyers – Government Edition</title>
<link rel="stylesheet" href="https://fonts.googleapis.com/css2?family=Poppins:wght@400;500;600;700&display=swap">
<style>
  :root{
    --backdrop:#a2a2a2;
    --crimson:#891a1e;
    --crimson-deep:#7a1519;
    --olive:#7f6e2c;
    --olive-light:#958336;
    --ink:#1d1d1d;
    --paper:#ffffff;
    --sky:#b9cde3;
    --stone:#c9ccd1;
  }
  *{box-sizing:border-box;margin:0;padding:0}
  html,body{width:1200px;height:852px;overflow:hidden;background:var(--backdrop);font-family:"Poppins",sans-serif;color:var(--ink)}
  .canvas{position:relative;width:1200px;height:852px}
  .flyer{position:absolute;width:450px;height:582px;background:var(--paper);overflow:hidden}
  .flyer--software{left:115px;top:101px}
  .flyer--services{left:592px;top:98px}
  .abs{position:absolute}

  /* hero photo */
  .hero-photo{position:absolute;left:0;top:0;width:450px;height:250px;
    background:linear-gradient(160deg,#dfe9f4 0%,var(--sky) 25%,#a9adb3 55%,#8d9096 80%,#6f7277 100%)}
  .hero-fade{position:absolute;left:0;top:0;width:330px;height:250px;
    background:linear-gradient(90deg,#fff 0%,#fff 45%,rgba(255,255,255,.85) 70%,rgba(255,255,255,0) 100%)}

  .brand-name{position:absolute;font-weight:600;font-size:12px;line-height:13px;color:var(--crimson);letter-spacing:.2px}
  .brand-name::before{content:"";display:inline-block;width:9px;height:9px;background:var(--olive);margin-right:5px;vertical-align:-1px}

  .headline{position:absolute;left:18px;top:74px;font-size:20.5px;line-height:22px;text-transform:uppercase;color:var(--olive);font-weight:500}
  .headline strong{color:var(--crimson);font-weight:700;display:block}
  .headline span{display:block}
  .hero-sub{position:absolute;left:18px;top:194px;width:170px;font-size:6.3px;line-height:11.8px;font-weight:500;color:#111}

  /* software middle */
  .feature-wheel{position:absolute;left:0;top:250px;width:450px;height:207px}
  .wheel-label{position:absolute;font-size:6.3px;line-height:7.6px;color:#fff}
  .wheel-label--center{text-align:center;transform:translateX(-50%)}
  .product-name{position:absolute;left:20px;top:76px;font-size:22px;font-weight:700;color:var(--crimson);letter-spacing:-.5px}

  .benefits-title{position:absolute;left:289px;top:267px;font-size:13.5px;line-height:16.5px;text-transform:uppercase}
  .benefits-title strong{color:var(--crimson);font-weight:700;display:block}
  .benefits-title span{color:var(--olive);font-weight:500;display:block}

  .rule{position:absolute;height:2.4px;width:22px;background:var(--olive)}
  .rule::after{content:"";position:absolute;left:24px;top:0;width:10px;height:2.4px;
    background:repeating-linear-gradient(100deg,var(--olive) 0 1.2px,transparent 1.2px 2.6px)}
  .rule--light{background:#fff}
  .rule--light::after{background:repeating-linear-gradient(100deg,#fff 0 1.2px,transparent 1.2px 2.6px)}

  .checklist{position:absolute;list-style:none}
  .checklist li{position:relative;padding-left:12px;font-size:7.1px;line-height:8.4px}
  .checklist li svg{position:absolute;left:0;top:.5px;width:7.5px;height:7.5px}
  .checklist--benefits{left:294px;top:429px}
  .checklist--benefits li{margin-bottom:6.3px}

  /* provides band */
  .provides{position:absolute;left:0;top:457px;width:450px;height:71px;background:linear-gradient(90deg,var(--olive),var(--olive-light) 60%,var(--olive))}
  .provides-title{position:absolute;left:26px;top:14px;font-size:13.5px;line-height:16px;color:#fff;text-transform:uppercase}
  .provides-title strong{font-weight:700;display:block}
  .provides-title span{font-weight:400;display:block}
  .divider{position:absolute;width:1px;background:rgba(255,255,255,.45)}
  .provide-item{position:absolute;top:22px;width:60px;margin-left:-30px;text-align:center;color:#fff;font-size:7px;line-height:8.6px;font-weight:500}
  .provide-item svg{display:block;margin:0 auto 4px;width:16px;height:16px}

  /* contact bar */
  .contact{position:absolute;left:0;width:450px;height:54px;background:var(--crimson);color:#fff}
  .contact-title{position:absolute;left:18px;top:7px;font-size:14.5px;line-height:16.5px;text-transform:uppercase}
  .contact-title strong{font-weight:700;display:block}
  .contact-title span{font-weight:400;display:block}
  .contact-phone{position:absolute;top:19px;font-size:11.5px;font-weight:500;display:flex;align-items:center;gap:5px}
  .contact-web{position:absolute;top:21px;font-size:7.6px;font-weight:500;display:flex;align-items:center;gap:8px}
  .contact-address{position:absolute;top:18px;font-size:6.5px;line-height:8px;font-weight:500;display:flex;align-items:center;gap:7px}

  /* services rows */
  .service-row{position:absolute;left:0;width:450px}
  .service-row--olive{background:var(--olive);color:#fff}
  .service-title{position:absolute;left:18px;font-size:10.8px;line-height:12.5px;font-weight:600;text-transform:uppercase;color:var(--crimson)}
  .service-row--olive .service-title{color:#fff}
  .service-copy{position:absolute;width:122px;font-size:7.4px;line-height:11.8px}
  .service-list-head{position:absolute;font-size:6.9px;font-weight:700;text-transform:uppercase;color:var(--crimson)}
  .service-row--olive .service-list-head{color:#fff}
  .checklist--service li{font-size:7.4px;line-height:8.2px;margin-bottom:6.5px}
  .service-icon{position:absolute;width:26px;height:26px}
</style>
</head>
<body>
<div class="canvas">

  <!-- ================= SOFTWARE FLYER ================= -->
  <section class="flyer flyer--software">
    <div class="hero-photo" role="img" aria-label="Photo looking up at a stone government building with columns and an American flag"></div>
    <div class="hero-fade"></div>

    <div class="brand-name" style="left:18px;top:38px">Harlow Partners</div>

    <h1 class="headline">
      <strong>Transition your</strong>
      <strong>inefficient</strong>
      <span>filing system</span>
      <span>to a paperless</span>
      <span>operation</span>
    </h1>
    <p class="hero-sub">Electronic FOIA Requests, Workflows, and Digital Document Management for Government Agencies and Municipalities</p>

    <!-- feature wheel -->
    <div class="feature-wheel">
      <svg class="abs" style="left:0;top:0" width="450" height="207" viewBox="0 0 450 207">
        <rect width="450" height="207" fill="var(--crimson)"/>
        <path d="M0,40 C55,30 118,48 126,93 C133,135 80,156 0,150 Z" fill="#fff"/>
        <polygon points="275,0 281,0 231,207 222,207" fill="var(--olive)"/>
        <polygon points="281,0 450,0 450,207 231,207" fill="#fff"/>
        <g fill="var(--olive)" stroke="#fff" stroke-width="1.2" stroke-dasharray="1.2 1.6">
          <circle cx="38" cy="43" r="17"/>
          <circle cx="88" cy="43" r="17"/>
          <circle cx="130" cy="77" r="17"/>
          <circle cx="128" cy="131" r="17"/>
          <circle cx="38" cy="158" r="17"/>
          <circle cx="87" cy="160" r="17"/>
        </g>
        <g fill="none" stroke="#fff" stroke-width="1.1" stroke-linecap="round" stroke-linejoin="round">
          <circle cx="34" cy="39" r="2.5"/><circle cx="42" cy="39" r="2.5"/><path d="M29,50 q5-6 10 0 M37,50 q5-6 10 0"/>
          <rect x="81" y="38" width="14" height="10" rx="1"/><path d="M84,45 l3-2 2 2 4-5"/>
          <rect x="124" y="70" width="12" height="14" rx="1"/><path d="M127,75 h6 M127,78 h6 M127,81 h4"/>
          <path d="M121,135 a7,7 0 1 1 14,0"/><path d="M128,135 l3-4"/>
          <rect x="32" y="152" width="12" height="9" rx="1"/><path d="M30,161 h16 v4 h-16 z"/>
          <rect x="81" y="153" width="10" height="13" rx="1"/><path d="M84,157 h4 M84,160 h4 M90,163 l4-4"/>
        </g>
      </svg>
      <div class="wheel-label wheel-label--center" style="left:38px;top:11px">HR<br>Onboarding</div>
      <div class="wheel-label" style="left:111px;top:39px">eSigning</div>
      <div class="wheel-label" style="left:154px;top:71px">Scanning &amp; Database<br>Conversion</div>
      <div class="wheel-label" style="left:154px;top:127px">Mileage &amp; Expense<br>Tracking</div>
      <div class="wheel-label" style="left:111px;top:163px">Electronic Forms &amp;<br>Workflows</div>
      <div class="wheel-label wheel-label--center" style="left:38px;top:183px">Document<br>Archive</div>
      <div class="product-name">Brelmont</div>
    </div>

    <h2 class="benefits-title"><strong>Brelmont Software</strong><span>Benefits</span></h2>
    <div class="rule" style="left:289px;top:313px"></div>

    <ul class="checklist checklist--benefits" style="top:329px">
      <li><svg viewBox="0 0 10 10"><circle cx="5" cy="5" r="5" fill="var(--crimson)"/><path d="M2.6,5.2 4.4,7 7.6,3" stroke="#fff" stroke-width="1.3" fill="none"/></svg>Paperless HR System</li>
      <li><svg viewBox="0 0 10 10"><circle cx="5" cy="5" r="5" fill="var(--crimson)"/><path d="M2.6,5.2 4.4,7 7.6,3" stroke="#fff" stroke-width="1.3" fill="none"/></svg>Applicant Tracking</li>
      <li><svg viewBox="0 0 10 10"><circle cx="5" cy="5" r="5" fill="var(--crimson)"/><path d="M2.6,5.2 4.4,7 7.6,3" stroke="#fff" stroke-width="1.3" fill="none"/></svg>Contract/Salary Notice<br>Management</li>
      <li><svg viewBox="0 0 10 10"><circle cx="5" cy="5" r="5" fill="var(--crimson)"/><path d="M2.6,5.2 4.4,7 7.6,3" stroke="#fff" stroke-width="1.3" fill="none"/></svg>Professional Development</li>
      <li><svg viewBox="0 0 10 10"><circle cx="5" cy="5" r="5" fill="var(--crimson)"/><path d="M2.6,5.2 4.4,7 7.6,3" stroke="#fff" stroke-width="1.3" fill="none"/></svg>Mileage &amp; Expense Tracking</li>
      <li><svg viewBox="0 0 10 10"><circle cx="5" cy="5" r="5" fill="var(--crimson)"/><path d="M2.6,5.2 4.4,7 7.6,3" stroke="#fff" stroke-width="1.3" fill="none"/></svg>Electronic Forms and Workflows</li>
      <li><svg viewBox="0 0 10 10"><circle cx="5" cy="5" r="5" fill="var(--crimson)"/><path d="M2.6,5.2 4.4,7 7.6,3" stroke="#fff" stroke-width="1.3" fill="none"/></svg>Collect Digital Signatures</li>
      <li><svg viewBox="0 0 10 10"><circle cx="5" cy="5" r="5" fill="var(--crimson)"/><path d="M2.6,5.2 4.4,7 7.6,3" stroke="#fff" stroke-width="1.3" fill="none"/></svg>Accept Credit Cards</li>
    </ul>

    <div class="provides">
      <h2 class="provides-title"><strong>Brelmont</strong><span>Provides</span></h2>
      <div class="rule rule--light" style="left:26px;top:52px"></div>
      <div class="divider" style="left:118px;top:10px;height:52px"></div>
      <div class="provide-item" style="left:154px">
        <svg viewBox="0 0 16 16" fill="#fff"><rect x="2" y="3" width="12" height="4" rx="1"/><rect x="2" y="8" width="12" height="6" rx="1"/><rect x="6" y="10" width="4" height="1.4" fill="var(--olive)"/></svg>Unlimited<br>Storage</div>
      <div class="provide-item" style="left:216px">
        <svg viewBox="0 0 16 16" fill="none" stroke="#fff" stroke-width="1.4"><circle cx="6" cy="8" r="4"/><path d="M10,5 h5 M10,8 h5 M10,11 h5"/></svg>Web-Based<br>Access</div>
      <div class="provide-item" style="left:277px">
        <svg viewBox="0 0 16 16" fill="#fff"><circle cx="8" cy="8" r="5"/><circle cx="8" cy="8" r="2" fill="var(--olive)"/><rect x="7" y="1" width="2" height="3"/><rect x="7" y="12" width="2" height="3"/><rect x="1" y="7" width="3" height="2"/><rect x="12" y="7" width="3" height="2"/></svg>Disaster<br>Recovery</div>
      <div class="provide-item" style="left:338px">
        <svg viewBox="0 0 16 16" fill="none" stroke="#fff" stroke-width="1.3"><rect x="4" y="2" width="8" height="7"/><path d="M3,9 h10 v3 h-10 z M5,12 v3 M8,12 v3 M11,12 v3"/></svg>Document<br>Security</div>
      <div class="provide-item" style="left:399px">
        <svg viewBox="0 0 16 16" fill="none" stroke="#fff" stroke-width="1.3"><path d="M8,3 14,6 8,9 2,6 Z M2,9 8,12 14,9 M2,12 8,15 14,12"/></svg>Records<br>Retention</div>
    </div>

    <div class="contact" style="top:528px">
      <h2 class="contact-title"><strong>Contact</strong><span>Us</span></h2>
      <div class="rule rule--light" style="left:18px;top:45px"></div>
      <div class="divider" style="left:97px;top:9px;height:36px"></div>
      <div class="contact-phone" style="left:108px">
        <svg width="8" height="8" viewBox="0 0 10 10"><path d="M2,1 4,1 5,3.5 3.8,4.5 Q4.8,6.3 6,6.5 L7,5.2 9.5,6.2 9.3,8.5 Q3,9 1.2,2.4Z" fill="#fff"/></svg>(555) 318-2070</div>
      <div class="divider" style="left:221px;top:9px;height:36px"></div>
      <div class="contact-web" style="left:232px">
        <svg width="11" height="11" viewBox="0 0 12 12" fill="none" stroke="#fff" stroke-width=".9"><circle cx="6" cy="6" r="5"/><ellipse cx="6" cy="6" rx="2.2" ry="5"/><path d="M1,6 h10 M2,3.5 h8 M2,8.5 h8"/></svg>www.brelmont.com</div>
      <div class="divider" style="left:324px;top:9px;height:36px"></div>
      <div class="contact-address" style="left:340px">
        <svg width="9" height="12" viewBox="0 0 9 12"><path d="M4.5,0 A4.5,4.5 0 0 1 9,4.5 C9,7.5 4.5,12 4.5,12 S0,7.5 0,4.5 A4.5,4.5 0 0 1 4.5,0Z" fill="#fff"/><circle cx="4.5" cy="4.4" r="1.6" fill="var(--crimson)"/></svg>
        <span>410 Commerce Drive<br>Fairview, Ohio 44000</span></div>
    </div>
  </section>

  <!-- ================= SERVICES FLYER ================= -->
  <section class="flyer flyer--services">
    <div class="hero-photo" role="img" aria-label="Photo looking up at a stone government building with columns and an American flag"></div>
    <div class="brand-name" style="left:4px;top:28px">Harlow Partners</div>

    <!-- scanning -->
    <div class="service-row" style="top:250px;height:86px">
      <svg class="service-icon" style="left:18px;top:11px" viewBox="0 0 26 26" fill="none" stroke="var(--crimson)" stroke-width="1.1"><path d="M1,6 V1 H6 M20,1 H25 V6 M25,20 V25 H20 M6,25 H1 V20"/><rect x="7" y="4" width="12" height="17"/><path d="M10,8 h6 M10,11 h6 M10,14 h6"/><path d="M3,16 h20" stroke-dasharray="1.5 1"/></svg>
      <h2 class="service-title" style="top:45px">Document<br>Scanning Services</h2>
      <div class="rule" style="left:18px;top:76px"></div>
      <p class="service-copy" style="left:146px;top:9px">Fast, efficient process for the conversion of existing paper records to digital archives, increasing access and reducing onsite storage and costs.</p>
      <div class="service-list-head" style="left:290px;top:10px">Scanning services for any format:</div>
      <ul class="checklist checklist--service" style="left:290px;top:25px">
        <li><svg viewBox="0 0 10 10"><circle cx="5" cy="5" r="5" fill="var(--crimson)"/><path d="M2.6,5.2 4.4,7 7.6,3" stroke="#fff" stroke-width="1.3" fill="none"/></svg>Standard Office Documents</li>
        <li><svg viewBox="0 0 10 10"><circle cx="5" cy="5" r="5" fill="var(--crimson)"/><path d="M2.6,5.2 4.4,7 7.6,3" stroke="#fff" stroke-width="1.3" fill="none"/></svg>16mm, 35mm Roll Microfilm</li>
        <li><svg viewBox="0 0 10 10"><circle cx="5" cy="5" r="5" fill="var(--crimson)"/><path d="M2.6,5.2 4.4,7 7.6,3" stroke="#fff" stroke-width="1.3" fill="none"/></svg>Microfiche (Jackets or COM)</li>
        <li><svg viewBox="0 0 10 10"><circle cx="5" cy="5" r="5" fill="var(--crimson)"/><path d="M2.6,5.2 4.4,7 7.6,3" stroke="#fff" stroke-width="1.3" fill="none"/></svg>Large Format Documents/Drawings</li>
      </ul>
    </div>

    <!-- storage -->
    <div class="service-row service-row--olive" style="top:336px;height:100px">
      <svg class="service-icon" style="left:18px;top:18px" viewBox="0 0 26 26" fill="none" stroke="#fff" stroke-width="1.1"><path d="M3,3 h11 l4,4 v13 h-15 z"/><path d="M6,9 h9 M6,12 h9 M6,15 h6"/><circle cx="20" cy="20" r="3.5"/><path d="M20,14.5 v2 M20,23.5 v2 M14.5,20 h2 M23.5,20 h2"/></svg>
      <h2 class="service-title" style="top:50px">Document<br>Storage Services</h2>
      <div class="rule rule--light" style="left:18px;top:79px"></div>
      <p class="service-copy" style="left:146px;top:15px;width:116px">Solution for offsite document storage and retrieval to effectively store, manage, and safeguard your vital business records and documents.</p>
      <div class="service-list-head" style="left:290px;top:16px">A local, convenient solution:</div>
      <ul class="checklist checklist--service" style="left:290px;top:31px">
        <li><svg viewBox="0 0 10 10"><path d="M1.5,5.2 4,7.8 8.8,1.8" stroke="#fff" stroke-width="1.5" fill="none"/></svg>Free Up Office Space</li>
        <li><svg viewBox="0 0 10 10"><path d="M1.5,5.2 4,7.8 8.8,1.8" stroke="#fff" stroke-width="1.5" fill="none"/></svg>Reduce Costs</li>
        <li><svg viewBox="0 0 10 10"><path d="M1.5,5.2 4,7.8 8.8,1.8" stroke="#fff" stroke-width="1.5" fill="none"/></svg>Keep Records in a Fireproof,<br>Waterproof &amp; Wind-Safe Facility</li>
      </ul>
    </div>

    <!-- shredding -->
    <div class="service-row" style="top:436px;height:93px">
      <svg class="service-icon" style="left:14px;top:12px" viewBox="0 0 26 26" fill="none" stroke="var(--crimson)" stroke-width="1.1"><path d="M7,1 h9 l3,3 v8 h-12 z M9,5 h7 M9,8 h7"/><rect x="2" y="12" width="22" height="6" rx="1"/><path d="M5,18 v7 M8,18 v7 M11,18 v7 M14,18 v7 M17,18 v7 M20,18 v7"/></svg>
      <h2 class="service-title" style="top:47px">Secure Document<br>Shredding</h2>
      <div class="rule" style="left:18px;top:76px"></div>
      <p class="service-copy" style="left:143px;top:9px;width:118px">Safely and cost-effectively destroy unnecessary paper-based documents. One-time or recurring, our solutions are tailored to you.</p>
      <div class="service-list-head" style="left:286px;top:10px">Destroy unnecessary documents:</div>
      <ul class="checklist checklist--service" style="left:286px;top:25px">
        <li><svg viewBox="0 0 10 10"><circle cx="5" cy="5" r="5" fill="var(--crimson)"/><path d="M2.6,5.2 4.4,7 7.6,3" stroke="#fff" stroke-width="1.3" fill="none"/></svg>Protect confidential information</li>
        <li><svg viewBox="0 0 10 10"><circle cx="5" cy="5" r="5" fill="var(--crimson)"/><path d="M2.6,5.2 4.4,7 7.6,3" stroke="#fff" stroke-width="1.3" fill="none"/></svg>Reduce the cost of managing<br>information that is no longer useful</li>
        <li><svg viewBox="0 0 10 10"><circle cx="5" cy="5" r="5" fill="var(--crimson)"/><path d="M2.6,5.2 4.4,7 7.6,3" stroke="#fff" stroke-width="1.3" fill="none"/></svg>Ensure compliance with regulations<br>for information destruction</li>
      </ul>
    </div>

    <div class="contact" style="top:529px;height:53px">
      <h2 class="contact-title"><strong>Contact</strong><span>Us</span></h2>
      <div class="rule rule--light" style="left:18px;top:45px"></div>
      <div class="divider" style="left:96px;top:9px;height:36px"></div>
      <div class="contact-phone" style="left:108px">
        <svg width="8" height="8" viewBox="0 0 10 10"><path d="M2,1 4,1 5,3.5 3.8,4.5 Q4.8,6.3 6,6.5 L7,5.2 9.5,6.2 9.3,8.5 Q3,9 1.2,2.4Z" fill="#fff"/></svg>(555) 318-2070</div>
      <div class="divider" style="left:220px;top:9px;height:36px"></div>
      <div class="contact-web" style="left:232px">
        <svg width="11" height="11" viewBox="0 0 12 12" fill="none" stroke="#fff" stroke-width=".9"><circle cx="6" cy="6" r="5"/><ellipse cx="6" cy="6" rx="2.2" ry="5"/><path d="M1,6 h10 M2,3.5 h8 M2,8.5 h8"/></svg>www.brelmont.com</div>
      <div class="divider" style="left:324px;top:9px;height:36px"></div>
      <div class="contact-address" style="left:340px">
        <svg width="9" height="12" viewBox="0 0 9 12"><path d="M4.5,0 A4.5,4.5 0 0 1 9,4.5 C9,7.5 4.5,12 4.5,12 S0,7.5 0,4.5 A4.5,4.5 0 0 1 4.5,0Z" fill="#fff"/><circle cx="4.5" cy="4.4" r="1.6" fill="var(--crimson)"/></svg>
        <span>410 Commerce Drive<br>Fairview, Ohio 44000</span></div>
    </div>
  </section>

</div>
</body>
</html>
```